Revise our price listr for 2023

Please see attached price list with new prices to revise.
Please include new logo
Please add the text: Please note that prices are subject to change without prior notice.
Please remove prices from equipment with operator
Please add Under Commercial stone:
Fill Dirt $16.
Please add under Decorative Stone:
3/4" Barn Red Stone $127.
3/4" Yellow Ocean Gravel $140.
3/4" Delaware River Gravel $110.
1" Nutmeg Pebble $97.
Price list sending via email and customer in our lobby
Landscape and construction supply

```html
<!DOCTYPE html>
<html lang="en">
<head>
<meta charset="utf-8">
<title>Ridgeline Supply – 2023 Material Price List</title>
<link href="https://fonts.googleapis.com/css2?family=Alfa+Slab+One&family=Oswald:wght@700&family=Source+Sans+3:wght@400;600;700&display=swap" rel="stylesheet">
<style>
  :root{
    --maroon:#7a1f24;
    --green:#15964a;
    --panel:#ece4e2;
    --white:#ffffff;
    --ink:#1d1b1b;
    --rule:#8fbf9f;
    --body:"Source Sans 3", Arial, sans-serif;
    --slab:"Alfa Slab One", Georgia, serif;
    --cond:"Oswald", "Arial Narrow", sans-serif;
  }
  *{box-sizing:border-box;margin:0;padding:0}
  html,body{width:1200px;height:927px;overflow:hidden}
  body{font-family:var(--body);color:var(--ink);position:relative;background:#c9a27a}
  .stone-backdrop{position:absolute;inset:0;
    background:radial-gradient(ellipse at 30% 60%,#d9b892 0%,#c49a6e 45%,#a97d57 100%)}
  .header-photo{position:absolute;left:0;top:0;width:798px;height:254px;
    background:linear-gradient(100deg,#f2f1ef 0%,#e4e2df 30%,#b89270 46%,#8a6a4f 55%,#6f7a52 68%,#9a8f86 80%,#a3558f 92%,#4f6b3a 100%)}
  .brand{position:absolute;left:104px;top:62px;width:200px;display:flex;align-items:center;gap:8px}
  .brand-dot{width:22px;height:22px;border-radius:50%;background:var(--maroon)}
  .brand-name{font-family:var(--slab);font-size:21px;color:var(--maroon);line-height:1}
  .year{position:absolute;left:0;width:406px;top:124px;text-align:center;font-family:var(--slab);font-size:46px;color:var(--maroon);line-height:1}
  .doc-title{position:absolute;left:0;width:406px;top:166px;text-align:center;font-family:var(--cond);font-weight:700;font-size:33px;color:var(--maroon);line-height:1;letter-spacing:-0.3px}
  .notice{position:absolute;left:15px;top:216px;width:370px;height:38px;background:var(--green);color:var(--white);
    font-weight:700;font-size:13.2px;line-height:14px;text-align:center;padding-top:5px;text-transform:uppercase}
  .sheet{position:absolute;background:var(--white)}
  .sheet-left{left:15px;top:254px;width:370px;height:649px}
  .sheet-mid{left:415px;top:237px;width:371px;height:666px}
  .sheet-right{left:813px;top:26px;width:371px;height:877px}
  .group{position:absolute;background:var(--panel)}
  .tab{position:absolute;background:var(--maroon);color:var(--white);font-family:var(--slab);font-size:17px;line-height:18px;
    display:flex;align-items:center;justify-content:center;writing-mode:vertical-rl;transform:rotate(180deg);text-align:center}
  .heading{position:absolute;background:var(--maroon);color:var(--white);font-family:var(--slab);font-size:17px;letter-spacing:1px;
    display:flex;align-items:center;justify-content:center}
  .rows{position:absolute;list-style:none}
  .row{display:flex;align-items:center;height:var(--rh);font-size:14.5px;padding-left:31px}
  .name{white-space:nowrap}
  .dots{flex:1;border-bottom:1.4px dotted var(--ink);margin:0 21px 0 4px;transform:translateY(4px)}
  .price{width:53px;height:21px;background:var(--maroon);color:var(--white);display:flex;align-items:center;justify-content:center;font-size:14.5px}
  .row.multi{height:auto;align-items:flex-end;font-size:14.5px;line-height:13.5px;margin-top:5px}
  .multi-lines{flex:1;margin-right:21px}
  .multi-lines .ln{display:flex}
  .multi-lines .dots{margin-right:0}
  .price.quote{height:44px;line-height:16px;text-align:center;flex-direction:column;font-size:14px;align-self:center}
  .equip-box{position:absolute;left:841px;top:63px;width:317px;height:650px;background:var(--panel)}
  .equip-title{position:absolute;left:897px;top:41px;width:212px;height:46px;background:var(--maroon);color:var(--white);
    font-family:var(--slab);font-size:13px;letter-spacing:1.2px;line-height:16px;text-align:center;padding-top:7px}
  .equip-call{position:absolute;left:897px;top:87px;width:212px;height:26px;background:var(--green);color:var(--white);
    font-weight:700;font-size:15px;text-align:center;line-height:26px}
  .spec{position:absolute;left:852px;width:294px;list-style:none;border-bottom:1px solid var(--rule)}
  .spec li{height:19.8px;border-top:1px solid var(--rule);font-size:14.5px;line-height:19px;padding-left:5px;display:flex;white-space:nowrap}
  .spec .col{width:164px}
  .bar{position:absolute;left:852px;width:294px;height:24px;background:var(--maroon);color:var(--white);font-weight:700;font-size:15px;line-height:24px;padding-left:6px}
  .promo-pill{position:absolute;left:878px;top:736px;width:242px;height:42px;border-radius:21px;background:var(--maroon);
    display:flex;align-items:center;gap:14px;padding-left:18px;color:var(--white);font-family:var(--slab);font-size:16px;letter-spacing:1px}
  .promo-text{position:absolute;left:813px;top:790px;width:371px;text-align:center;font-weight:700;font-size:16px;line-height:18px}
  .promo-text .green{color:var(--green);font-weight:600}
  .footer{position:absolute;left:813px;top:868px;width:371px;height:35px;background:var(--green);color:var(--white);
    font-weight:700;font-size:14.5px;text-align:center;line-height:35px;text-transform:uppercase;letter-spacing:-0.2px}
</style>
</head>
<body>
  <div class="stone-backdrop" role="img" aria-label="Sandstone rock surface texture"></div>
  <div class="header-photo" role="img" aria-label="Piles of white salt, smooth river stones and a cobblestone garden stairway lined with purple flowers"></div>

  <div class="brand"><span class="brand-dot"></span><span class="brand-name">Ridgeline Supply</span></div>
  <div class="year">2023</div>
  <div class="doc-title">MATERIAL PRICE LIST</div>

  <div class="sheet sheet-left"></div>
  <div class="sheet sheet-mid"></div>
  <div class="sheet sheet-right"></div>

  <div class="notice">Please note that prices are subject to change<br>without prior notice.</div>

  <section class="group" style="left:54px;top:270px;width:319px;height:134px">
    <ul class="rows" style="--rh:24.2px;top:5px;left:0;width:317px">
      <li class="row"><span class="name">Sandy Loam</span><span class="dots"></span><span class="price">$30</span></li>
      <li class="row"><span class="name">Topsoil-Screened</span><span class="dots"></span><span class="price">$42</span></li>
      <li class="row"><span class="name">Garden Soil</span><span class="dots"></span><span class="price">$52</span></li>
      <li class="row"><span class="name">Mushroom Dirt</span><span class="dots"></span><span class="price">$55</span></li>
      <li class="row"><span class="name">Compost (Leaf &amp; Grass)</span><span class="dots"></span><span class="price">$55</span></li>
    </ul>
  </section>
  <div class="tab" style="left:30px;top:301px;width:45px;height:73px">SOIL</div>

  <section class="group" style="left:55px;top:423px;width:318px;height:156px">
    <ul class="rows" style="--rh:24.3px;top:3px;left:0;width:317px">
      <li class="row"><span class="name">Mulch-Dyed Black</span><span class="dots"></span><span class="price">$42</span></li>
      <li class="row"><span class="name">Mulch-Dyed Red</span><span class="dots"></span><span class="price">$42</span></li>
      <li class="row"><span class="name">Mulch-Dyed Brown</span><span class="dots"></span><span class="price">$42</span></li>
      <li class="row"><span class="name">Mulch-Natural Light Brown</span><span class="dots"></span><span class="price">$38</span></li>
      <li class="row"><span class="name">Mulch-Dark Triple Ground</span><span class="dots"></span><span class="price">$44</span></li>
      <li class="row"><span class="name">Mulch Cedar</span><span class="dots"></span><span class="price">$55</span></li>
    </ul>
  </section>
  <div class="tab" style="left:32px;top:440px;width:44px;height:111px">MULCH</div>

  <section class="group" style="left:55px;top:599px;width:318px;height:281px">
    <ul class="rows" style="--rh:24.4px;top:3px;left:0;width:317px">
      <li class="row"><span class="name">White Limestone #1 [1/4”-1/2”]</span><span class="dots"></span><span class="price">$95</span></li>
      <li class="row"><span class="name">White Limestone #2 [1/2”-3/4”]</span><span class="dots"></span><span class="price">$97.50</span></li>
      <li class="row"><span class="name">River Rock #2 [3/4”] Round</span><span class="dots"></span><span class="price">$50</span></li>
      <li class="row"><span class="name">River Rock-Medium [2/3”]</span><span class="dots"></span><span class="price">$95</span></li>
      <li class="row"><span class="name">River Rounds [4-6”]</span><span class="dots"></span><span class="price">$90</span></li>
      <li class="row"><span class="name">Pea Gravel</span><span class="dots"></span><span class="price">$50</span></li>
      <li class="row"><span class="name">Berkshire Blend</span><span class="dots"></span><span class="price">$50</span></li>
      <li class="row"><span class="name">3/4" Barn Red Stone</span><span class="dots"></span><span class="price">$127</span></li>
      <li class="row"><span class="name">3/4" Yellow Ocean Gravel</span><span class="dots"></span><span class="price">$140</span></li>
      <li class="row"><span class="name">3/4" Delaware River Gravel</span><span class="dots"></span><span class="price">$110</span></li>
      <li class="row"><span class="name">1" Nutmeg Pebble</span><span class="dots"></span><span class="price">$97</span></li>
    </ul>
  </section>
  <div class="tab" style="left:32px;top:665px;width:44px;height:145px">DECORATIVE<br>STONE</div>

  <section class="group" style="left:449px;top:268px;width:318px;height:88px">
    <ul class="rows" style="--rh:24.3px;top:29px;left:0;width:317px">
      <li class="row"><span class="name">Masonary/Pool Sand</span><span class="dots"></span><span class="price">$45</span></li>
      <li class="row"><span class="name">Bedding Sand</span><span class="dots"></span><span class="price">$37</span></li>
    </ul>
  </section>
  <div class="heading" style="left:540px;top:252px;width:134px;height:42px">SAND</div>

  <section class="group" style="left:449px;top:375px;width:318px;height:253px">
    <ul class="rows" style="--rh:24.3px;top:3px;left:0;width:317px">
      <li class="row"><span class="name">Item #4</span><span class="dots"></span><span class="price">$42</span></li>
      <li class="row"><span class="name">#1 Stone (1/2”)</span><span class="dots"></span><span class="price">$45</span></li>
      <li class="row"><span class="name">#2 Stone (3/4” 1”)</span><span class="dots"></span><span class="price">$45</span></li>
      <li class="row"><span class="name">#3 (1.5* 2*)</span><span class="dots"></span><span class="price">$45</span></li>
      <li class="row"><span class="name">Stone Chip (fine)</span><span class="dots"></span><span class="price">$40</span></li>
      <li class="row"><span class="name">Stone Dust (xtra fine)</span><span class="dots"></span><span class="price">$47</span></li>
      <li class="row"><span class="name">Shale When Available</span><span class="dots"></span><span class="price">Call</span></li>
      <li class="row"><span class="name">Bank Run Fill (Dirt &amp; Cobble)</span><span class="dots"></span><span class="price">$18</span></li>
      <li class="row"><span class="name">Crusher Run</span><span class="dots"></span><span class="price">$42</span></li>
      <li class="row"><span class="name">Fill Dirt</span><span class="dots"></span><span class="price">$16</span></li>
    </ul>
  </section>
  <div class="tab" style="left:425px;top:415px;width:45px;height:165px">COMMERCIAL<br>STONE</div>

  <section class="group" style="left:446px;top:671px;width:318px;height:52px">
    <ul class="rows" style="--rh:24.3px;top:22px;left:0;width:317px">
      <li class="row"><span class="name">Treated Salt Green</span><span class="dots"></span><span class="price">$165</span></li>
    </ul>
  </section>
  <div class="heading" style="left:540px;top:650px;width:134px;height:42px">SEASONAL</div>

  <section class="group" style="left:446px;top:746px;width:318px;height:133px">
    <ul class="rows" style="--rh:24.5px;top:6px;left:0;width:317px">
      <li class="row"><span class="name">Local (Small Truck)</span><span class="dots"></span><span class="price">$165</span></li>
      <li class="row"><span class="name">Local (Medium Truck)</span><span class="dots"></span><span class="price">$75</span></li>
      <li class="row"><span class="name">Local (Large Truck)</span><span class="dots"></span><span class="price">$115</span></li>
      <li class="row multi">
        <div class="multi-lines">
          <div class="ln"><span class="name">Local Deliveries 7 Mile Radius</span></div>
          <div class="ln"><span class="name">Excluding the Material</span><span class="dots" style="transform:translateY(2px)"></span></div>
          <div class="ln"><span class="name">Non Local</span><span class="dots" style="transform:translateY(2px)"></span></div>
        </div>
        <span class="price quote"><span>Call For</span><span>Quote</span></span>
      </li>
    </ul>
  </section>
  <div class="tab" style="left:429px;top:755px;width:42px;height:113px">DELIVERY<br>CHARGES</div>

  <div class="equip-box"></div>
  <div class="equip-title">EQUIPMENT WITH<br>OPERATOR AVAILABLE</div>
  <div class="equip-call">CALL FOR PRICING</div>

  <ul class="spec" style="top:138px">
    <li>Onsite Mobile Grinding/Tub Grinding</li>
    <li>Forestry Mulching</li>
    <li>Skid Steer: (Rubber Track)</li>
    <li>Available Attachment</li>
    <li><span class="col">Landscape Rake</span><span>3/4 Yard Bucket</span></li>
    <li><span class="col">Forestry Mulching</span><span>Hydraulic Auger</span></li>
    <li><span class="col"></span><span>Grapple Bucket</span></li>
  </ul>

  <div class="bar" style="top:294px">EXCAVATUR</div>
  <ul class="spec" style="top:334px">
    <li>35 Class (7,500bs)</li>
    <li>60 Class (14,000bs)</li>
    <li>140 Class (45,500bs)</li>
    <li>160 Class (38,500bs)</li>
    <li>250 Class (60,000bs)</li>
  </ul>

  <div class="bar" style="top:452px">BULL DOZER</div>
  <ul class="spec" style="top:492px">
    <li>450 Class (18,000bs)</li>
    <li>700 Class (30,000bs)</li>
    <li>Vibratory Roller</li>
  </ul>

  <div class="bar" style="top:570px">Rock Hammer</div>
  <ul class="spec" style="top:611px">
    <li>Hydraulic Rock Hammer on 160 Class excavator.</li>
    <li>Additional mobilization fee for 1st day</li>
    <li>Tri-Axle Dump</li>
    <li>Dump Trailer</li>
  </ul>

  <div class="promo-pill">
    <svg width="36" height="30" viewBox="0 0 36 30" aria-hidden="true">
      <path d="M4 12 L20 5 L20 24 L4 18 Z" fill="#fff"/>
      <rect x="1" y="11" width="5" height="8" rx="1" fill="#fff"/>
      <path d="M7 18 L10 27 L13 27 L11 19" fill="#fff"/>
      <path d="M24 9 L30 5 M25 15 L32 15 M24 21 L30 25" stroke="#fff" stroke-width="2" stroke-linecap="round"/>
    </svg>
    <span>DID YOU KNOW?</span>
  </div>
  <p class="promo-text">We Offer Onside Tub Grinding<br>&amp;<br><span class="green">We are a GREEN RECYCLING Location!</span></p>

  <div class="footer">Non local call for pricing. Thank you</div>
</body>
</html>
```